Summit Ridge Business Card

Side 1: Summit Ridge Logo (logo without Maltese cross) with industrial rope rescue related theme. Our company services - TRAINING - Fire Training, Confined Space Rescue Training, Rope Rescue training, Hazmat Training, Incident Command, EMS, Pump Operations Training. Website - summitridgeexample.com.
Side 2: Summit Ridge Fire Department Logo (logo with Maltese cross) with Firefighter related theme. Company (division) services - FIELD SERVICES - Fire Department, Stand-by Rescue, Safety, EMS, Planning. "Supporting the Emergency Response Community Since 1967"

Add contact information wherever it makes since (Name, Email, Phone).
I would like it to represent the Summit Ridge Fire Department Logo as a division not as a separate entity without saying it, possibly by depicting it in the background of Side 2 instead of being a standalone picture like the logo on Side 1.

```html
<!DOCTYPE html>
<html lang="en">
<head>
<meta charset="utf-8">
<title>Summit Ridge Business Card</title>
<link href="https://fonts.googleapis.com/css2?family=Montserrat:wght@400;500;600;700;800&display=swap" rel="stylesheet">
<style>
  :root{
    --page:#2b2c2f;
    --card-dark:#38393b;
    --card-deep:#2a2a2c;
    --red:#ec1c24;
    --orange:#ef5a2a;
    --orange-soft:#f08a5d;
    --white:#ffffff;
    --muted:#d9d9d9;
  }
  *{box-sizing:border-box;margin:0;padding:0}
  html,body{width:1200px;height:952px;overflow:hidden;background:var(--page);font-family:"Montserrat",sans-serif;color:var(--white)}
  .sheet{width:1200px;height:952px;display:flex;flex-direction:column;align-items:center;justify-content:center;gap:56px}
  .card{position:relative;width:700px;height:400px;border-radius:22px;overflow:hidden;box-shadow:0 14px 30px rgba(0,0,0,.45)}

  /* Side 1 */
  .card--training{background:var(--card-dark)}
  .card--training .scene{position:absolute;inset:0;background:radial-gradient(ellipse at 40% 45%,rgba(70,70,72,.9),rgba(56,57,59,0) 65%)}
  .brand{position:absolute;display:flex;align-items:center;gap:12px}
  .brand__mark{width:34px;height:34px;background:var(--red);border-radius:4px}
  .brand__name{font-weight:800;font-size:34px;letter-spacing:1px;color:var(--white);line-height:1}
  .card--training .brand{left:70px;top:70px}
  .web-band{position:absolute;left:0;top:170px;width:440px;height:38px;background:var(--red);display:flex;align-items:center;padding-left:40px;font-size:15px;font-weight:500;letter-spacing:7px}
  .service-list{position:absolute;list-style:none}
  .service-list li{position:relative;padding-left:14px;line-height:1.55}
  .service-list li::before{content:"";position:absolute;left:0;top:.65em;width:5px;height:5px;border-radius:50%;background:var(--red)}
  .card--training .service-list{left:430px;top:60px;font-size:14.5px;font-weight:500}
  .card--training .service-list li:first-child{font-weight:600;letter-spacing:.5px}

  /* Side 2 */
  .card--field{background:linear-gradient(135deg,var(--orange) 0%,#a8452a 32%,var(--card-deep) 68%)}
  .card--field .scene{position:absolute;left:200px;top:90px;width:300px;height:310px;background:radial-gradient(ellipse at 50% 50%,rgba(90,88,86,.55),rgba(42,42,44,0) 70%)}
  .card--field .brand{left:40px;top:42px;flex-direction:column;align-items:flex-start;gap:6px}
  .brand__division{font-size:11px;letter-spacing:5px;font-weight:500;border-top:1.5px solid var(--white);padding-top:5px}
  .card--field .brand__name{font-size:30px}
  .tagline{position:absolute;left:40px;top:150px;font-size:15px;font-weight:500;line-height:1.45;color:#ffe2d2}
  .card--field .service-list{font-size:14px;font-weight:600;letter-spacing:.4px}
  .service-list--field{left:210px;top:262px}
  .service-list--extra{left:470px;top:262px}
  .contact{position:absolute;right:40px;top:44px;text-align:right}
  .contact__name{font-size:25px;font-weight:700;letter-spacing:.5px}
  .contact__name span{color:var(--red)}
  .contact__role{font-size:15px;font-weight:500;margin-top:2px}
  .contact__line{display:flex;justify-content:flex-end;align-items:center;gap:9px;font-size:13.5px;margin-top:9px}
  .contact__icon{width:20px;height:20px;background:var(--white);border-radius:3px;display:flex;align-items:center;justify-content:center}
</style>
</head>
<body>
<main class="sheet">

  <section class="card card--training">
    <div class="scene" role="img" aria-label="Faint industrial rope rescue photograph with ropes and harness gear"></div>
    <div class="brand">
      <span class="brand__mark"></span>
      <span class="brand__name">SUMMIT RIDGE</span>
    </div>
    <div class="web-band">summitridgeexample.com</div>
    <ul class="service-list">
      <li>TRAINING</li>
      <li>Fire Training</li>
      <li>Confined Space Rescue Training</li>
      <li>Rope Rescue training</li>
      <li>Hazmat Training</li>
      <li>Incident Command</li>
      <li>EMS</li>
      <li>Pump Operations Training</li>
    </ul>
  </section>

  <section class="card card--field">
    <div class="scene" role="img" aria-label="Firefighters spraying a hose through smoke"></div>
    <div class="brand">
      <span class="brand__name">SUMMIT RIDGE</span>
      <span class="brand__division">FIRE DEPARTMENT</span>
    </div>
    <p class="tagline">Supporting The<br>Emergency Response<br>Community Since 1967</p>
    <div class="contact">
      <p class="contact__name">DANIEL M. <span>HARLOW</span></p>
      <p class="contact__role">Managing Director</p>
      <p class="contact__line">+00 555 014 27
        <span class="contact__icon"><svg width="12" height="12" viewBox="0 0 24 24"><path fill="#ec1c24" d="M6.6 10.8a15 15 0 0 0 6.6 6.6l2.2-2.2a1 1 0 0 1 1-.25 11.4 11.4 0 0 0 3.6.57 1 1 0 0 1 1 1V20a1 1 0 0 1-1 1A17 17 0 0 1 3 4a1 1 0 0 1 1-1h3.5a1 1 0 0 1 1 1c0 1.25.2 2.45.57 3.57a1 1 0 0 1-.25 1z"/></svg></span>
      </p>
      <p class="contact__line">daniel@summitridgeexample.com
        <span class="contact__icon"><svg width="13" height="10" viewBox="0 0 26 20"><rect x="1" y="1" width="24" height="18" fill="none" stroke="#ec1c24" stroke-width="2.5"/><path d="M1 1l12 10L25 1" fill="none" stroke="#ec1c24" stroke-width="2.5"/></svg></span>
      </p>
    </div>
    <ul class="service-list service-list--field">
      <li>FIELD SERVICES</li>
      <li>FIRE DEPARTMENT</li>
      <li>STAND-BY RESCUE</li>
    </ul>
    <ul class="service-list service-list--extra">
      <li>SAFETY</li>
      <li>EMS</li>
      <li>PLANNING</li>
    </ul>
  </section>

</main>
</body>
</html>
```